Dwelvano - "Where Pest Control is Free for Life..." Please see pitch deck...

Project goal, that this is a reusable template, not a one-off card
Brand and design direction, follow the logo, use the brand palette (with a color swatch table), typography and layout guidance
The John Doe placeholder content as a clean field-by-field table (name, title, company, address, office, cell, fax, email, dwelvano.com)
Print specs, 3.5 × 2 in trim, 0.125 in bleed, 300 DPI, CMYK, crop marks
Deliverables, layered editable PSD (your primary ask) plus vector .AI/.EPS and a press-ready PDF/X-1a, with fonts packaged
What you'll provide (logo, colors, fonts)
Process and sign-off, concept first, then full file package on approval.
Populate every field with this John Doe placeholder data so we can see the layout fully built out. We will replace it per person.
Name John Doe
Title Title / Position
Company Dwelvano
Address 123 Main Street, Suite 100, Tallahassee, FL 32301
Office (850) 555-0100
Cell (850) 555-0123
Fax (850) 555-0199
Email johndoe@dwelvano.com
Website dwelvano.com

We need the working, editable source files so we can update them ourselves, plus a ready-to-print export:
1. Photoshop (.PSD) — fully layered and editable, with each contact field on its own labeled text layer. This is the primary requested format.
2. Vector source — the press-standard editable format, Adobe Illustrator (.AI) and/or .EPS, since vector is preferred for crisp text and logos at print.
3. Print-ready PDF — press-quality (PDF/X-1a), CMYK, with bleed and crop marks, both sides.
4. Packaged fonts and links — include or list all fonts used, and package any linked assets so the files open correctly on our end.

Why both PSD and vector
The PSD covers our request directly and is easy for us to edit. Vector (.AI/.EPS) is what most commercial printers actually prefer for type and logos because it stays razor-sharp at any size. Providing both keeps us flexible no matter which printer we use. Have fun and keep it modern and cool the designer of the logo did a great job, see what you can do.

```html
<!DOCTYPE html>
<html lang="en">
<head>
<meta charset="utf-8">
<title>Dwelvano Business Card</title>
<link href="https://fonts.googleapis.com/css2?family=Lato:wght@400&family=Montserrat:wght@500;700;800&display=swap" rel="stylesheet">
<style>
  :root {
    --stage: #1b1b1b;
    --card: #000000;
    --teal: #0db2c5;
    --white: #ffffff;
  }
  * { margin: 0; padding: 0; box-sizing: border-box; }
  html, body {
    width: 1200px;
    height: 1059px;
    overflow: hidden;
    background: var(--stage);
  }
  .canvas {
    position: relative;
    width: 1200px;
    height: 1059px;
  }
  .card {
    position: absolute;
    background: var(--card);
    border-radius: 18px;
    overflow: hidden;
  }
  .card--front { left: 254px; top: 85px; width: 691px; height: 396px; }
  .card--back  { left: 254px; top: 547px; width: 705px; height: 403px; }

  .wordmark {
    position: absolute;
    font-family: "Montserrat", sans-serif;
    font-weight: 800;
    color: var(--white);
    letter-spacing: -1px;
    line-height: 1;
    white-space: nowrap;
  }
  .card--front .wordmark { left: 24px; top: 50px; font-size: 60px; }
  .card--back .wordmark {
    left: 0; right: 0; top: 155px;
    text-align: center;
    font-size: 68px;
  }

  .holder {
    position: absolute;
    right: 27px;
    top: 22px;
    text-align: right;
  }
  .holder__name {
    font-family: "Montserrat", sans-serif;
    font-weight: 700;
    font-size: 26px;
    color: var(--teal);
    line-height: 1.1;
  }
  .holder__title {
    font-family: "Montserrat", sans-serif;
    font-weight: 500;
    font-size: 18px;
    color: var(--white);
    line-height: 1.3;
    margin-top: 2px;
  }
  .holder__bar {
    position: absolute;
    right: 0;
    top: 23px;
    width: 12px;
    height: 41px;
    background: var(--teal);
  }

  .brand-panel {
    position: absolute;
    left: 451px;
    top: 97px;
    width: 240px;
    height: 299px;
    background: var(--teal);
    border-radius: 10px 10px 18px 10px;
  }

  .contact {
    position: absolute;
    left: 24px;
    top: 194px;
    list-style: none;
    font-family: "Lato", sans-serif;
    font-size: 19px;
    color: var(--white);
  }
  .contact__item {
    display: flex;
    align-items: flex-start;
    height: 27.5px;
    line-height: 24px;
  }
  .contact__icon {
    width: 18px;
    height: 18px;
    margin: 3px 13px 0 0;
    flex: none;
    fill: var(--teal);
  }
  .contact__item--address { height: auto; }
</style>
</head>
<body>
<div class="canvas">

  <section class="card card--front" aria-label="Card front">
    <div class="wordmark">Dwelvano</div>

    <div class="holder">
      <div class="holder__name">JOHN DOE</div>
      <div class="holder__title">Owner</div>
    </div>
    <div class="holder__bar"></div>

    <div class="brand-panel" role="img" aria-label="Brand symbol area"></div>

    <ul class="contact">
      <li class="contact__item">
        <svg class="contact__icon" viewBox="0 0 24 24"><path d="M2 9c0-3 5-5 10-5s10 2 10 5v2h-5V8.5c-1.5-.6-3.2-.8-5-.8s-3.5.2-5 .8V11H2z M5 13l3-4h8l3 4v7H5z M12 13.5a2.5 2.5 0 1 0 0 5a2.5 2.5 0 1 0 0-5z"/></svg>
        <span>(850) 555-0100</span>
      </li>
      <li class="contact__item">
        <svg class="contact__icon" viewBox="0 0 24 24"><path d="M7 1h10a2 2 0 0 1 2 2v18a2 2 0 0 1-2 2H7a2 2 0 0 1-2-2V3a2 2 0 0 1 2-2zm0 3v14h10V4zm5 15.5a1.2 1.2 0 1 0 0 2.4a1.2 1.2 0 1 0 0-2.4z"/></svg>
        <span>(850) 555-0123</span>
      </li>
      <li class="contact__item">
        <svg class="contact__icon" viewBox="0 0 24 24"><path d="M2 7h4v15H2z M8 8h14v14H8z M10 2h9v5h-9z M10 11h10v3H10z M10 16h2v2h-2z M14 16h2v2h-2z M18 16h2v2h-2z M10 19h2v2h-2z M14 19h2v2h-2z M18 19h2v2h-2z"/></svg>
        <span>(850) 555-0199</span>
      </li>
      <li class="contact__item">
        <svg class="contact__icon" viewBox="0 0 24 24"><path d="M2 5h20v2l-10 7L2 7z M2 9.5l10 7 10-7V19H2z"/></svg>
        <span>johndoe@dwelvano.com</span>
      </li>
      <li class="contact__item">
        <svg class="contact__icon" viewBox="0 0 24 24"><path d="M12 2a10 10 0 1 0 0 20a10 10 0 1 0 0-20zm-1 2.2c-1.5 1-3 1.2-3.5 2.8c-.4 1.4 1.2 2 2.3 2.6c1.3.7.7 2.3 1.7 3.2c1 .9 2.6.2 3 1.6c.4 1.3-.8 2.8-1.4 4c-.3.6.2 1.3.9 1.2A8 8 0 0 0 11 4.2zM4.3 9.5A8 8 0 0 0 9 19.4c.3-1.6-.4-3.2-1.4-4.4c-.9-1-.5-2.6-1.6-3.4c-.6-.5-1.4-1.2-1.7-2.1z"/></svg>
        <span>www.dwelvano.com</span>
      </li>
      <li class="contact__item contact__item--address">
        <svg class="contact__icon" viewBox="0 0 24 24"><path d="M12 1a8 8 0 0 0-8 8c0 6 8 14 8 14s8-8 8-14a8 8 0 0 0-8-8zm0 4.5a3.5 3.5 0 1 1 0 7a3.5 3.5 0 1 1 0-7z"/></svg>
        <span>123 Main Street, Suite 100,<br>Tallahassee, FL 32301</span>
      </li>
    </ul>
  </section>

  <section class="card card--back" aria-label="Card back">
    <div class="wordmark">Dwelvano</div>
  </section>

</div>
</body>
</html>
```